Telecommunications/Power civil contractor needs business card design

Were a new telecommunications/power underground civil contractor that is looking for a new business card design. Our company colours are silver or grey and orange. Feel free to use the white background logo or the black background logo.

Target Market(s)

Local contractors, utility companies, private sector mining/energy companies, developers.

Industry/Entity Type

Telecommunications

Contact Information for Business Card

Each card will need the following info:
Persons name:
Title:
E-mail:
Phone number:
Shop Address:
Mailing Address:

Requirements
Must have
• Each card will need the following info:
• Persons name:
• Title:
• E-mail:
• Phone number:
• Shop Address:
• Mailing Address:

```html
<!DOCTYPE html>
<html lang="en">
<head>
<meta charset="utf-8">
<title>Tek Line Contracting Inc – Business Card</title>
<link href="https://fonts.googleapis.com/css2?family=Open+Sans:wght@400;600;700;800&display=swap" rel="stylesheet">
<style>
  :root {
    --backdrop: #cbc3b6;
    --card: #111111;
    --card-back: #1a1a1a;
    --orange: #f26522;
    --grey: #8a8a8a;
    --light-grey: #b5b5b5;
  }
  * { margin: 0; padding: 0; box-sizing: border-box; }
  html, body {
    width: 1200px;
    height: 675px;
    overflow: hidden;
  }
  body {
    background: var(--backdrop);
    font-family: "Open Sans", Arial, sans-serif;
    position: relative;
  }
  .card {
    position: absolute;
    top: 187px;
    width: 520px;
    height: 300px;
    border-radius: 3px;
    box-shadow: 0 8px 20px rgba(0,0,0,0.35);
    overflow: hidden;
  }
  .card--front { left: 50px; background: var(--card); }
  .card--back { left: 630px; background: var(--card-back); }

  .brand {
    position: absolute;
    display: flex;
    flex-direction: column;
    align-items: center;
    text-align: center;
  }
  .brand__ring {
    flex: none;
    border: 3px solid var(--grey);
    border-radius: 50%;
  }
  .brand__name {
    color: var(--orange);
    font-weight: 800;
    text-transform: uppercase;
    line-height: 1.1;
    letter-spacing: 0.5px;
    white-space: nowrap;
  }
  .card--front .brand { left: 34px; top: 40px; gap: 8px; }
  .card--front .brand__ring { width: 46px; height: 46px; }
  .card--front .brand__name { font-size: 16px; }

  .card--back .brand {
    left: 50%;
    top: 50%;
    transform: translate(-50%, -50%);
    gap: 14px;
  }
  .card--back .brand__ring { width: 84px; height: 84px; border-width: 4px; }
  .card--back .brand__name { font-size: 28px; }

  .person {
    position: absolute;
    left: 300px;
    top: 36px;
  }
  .person__name {
    color: var(--orange);
    font-weight: 700;
    font-size: 13px;
  }
  .person__title {
    color: var(--grey);
    font-size: 12px;
    margin-top: 2px;
  }

  .contact {
    position: absolute;
    left: 250px;
    top: 150px;
    color: var(--light-grey);
    font-size: 12px;
    line-height: 1.6;
    list-style: none;
  }
  .contact__item { display: flex; align-items: center; gap: 7px; white-space: nowrap; }
  .contact__label { color: var(--orange); font-weight: 600; }
  .contact__icon { width: 12px; height: 12px; flex: none; }
</style>
</head>
<body>

  <section class="card card--front" aria-label="Business card front">
    <div class="brand">
      <span class="brand__ring" aria-hidden="true"></span>
      <span class="brand__name">Tek Line<br>Contracting Inc</span>
    </div>

    <div class="person">
      <p class="person__name">Morgan Hale</p>
      <p class="person__title">Managing Director</p>
    </div>

    <ul class="contact">
      <li class="contact__item"><span class="contact__label">Shop:</span> N. 8 Sample Street, Suite 200</li>
      <li class="contact__item">Ridgeton, WA 55555</li>
      <li class="contact__item"><span class="contact__label">Mail:</span> PO Box 410, Ridgeton, WA 55555</li>
      <li class="contact__item">
        <svg class="contact__icon" viewBox="0 0 12 12" aria-hidden="true">
          <path d="M2 1 L4.5 1 L5.5 3.5 L4 4.5 Q5 7 7.5 8 L8.5 6.5 L11 7.5 L11 10 Q6 11 3 8 Q1 5.5 2 1 Z" fill="var(--orange)"/>
        </svg>
        555.010.2020
      </li>
      <li class="contact__item">
        <svg class="contact__icon" viewBox="0 0 12 12" aria-hidden="true">
          <rect x="1" y="2.5" width="10" height="7" rx="1" fill="var(--orange)"/>
          <path d="M1.5 3 L6 6.5 L10.5 3" fill="none" stroke="var(--card)" stroke-width="1"/>
        </svg>
        info@teklinecontracting.com
      </li>
    </ul>
  </section>

  <section class="card card--back" aria-label="Business card back">
    <div class="brand">
      <span class="brand__ring" aria-hidden="true"></span>
      <span class="brand__name">Tek Line<br>Contracting Inc</span>
    </div>
  </section>

</body>
</html>
```